Quill Physical Therapy Website

I would need a clean modern website built to showcase my Physical therapy brand and services. I would need a simple but descriptive website that can ultimately connect my patients to my electronic medical portal so they may book an appointment..

```html
<!DOCTYPE html>
<html lang="en">
<head>
<meta charset="utf-8">
<title>Quill Physical Therapy &amp; Wellness</title>
<link rel="stylesheet" href="https://fonts.googleapis.com/css2?family=Montserrat:wght@400;500;600;700&family=Open+Sans:ital,wght@0,400;0,600;1,400&display=swap">
<style>
:root{
  --teal:#16877f;
  --teal-dark:#0f6f69;
  --teal-light:#2aa39a;
  --green:#7dc242;
  --green-light:#9ad15f;
  --ink:#1f2b36;
  --body:#5b6570;
  --mist:#eef3f3;
  --footer-bar:#ececec;
  --white:#ffffff;
}
*{margin:0;padding:0;box-sizing:border-box}
html,body{width:1200px;height:4135px;overflow:hidden;background:var(--white)}
body{position:relative;font-family:"Montserrat",sans-serif;color:var(--ink)}
.abs{position:absolute}
.photo{position:absolute}

/* header */
.site-header{position:absolute;left:0;top:0;width:1200px;height:100px;background:var(--white);z-index:5}
.brand{position:absolute;left:104px;top:22px;display:flex;align-items:center;gap:12px}
.brand-dot{width:48px;height:48px;border-radius:50%;background:var(--teal)}
.brand-name{font-weight:700;font-size:30px;color:var(--teal);letter-spacing:1px;line-height:1}
.brand-tag{display:block;font-weight:700;font-size:30px;color:var(--teal);}
.topbar{position:absolute;top:0;left:598px;display:flex;height:35px}
.topbar a{display:flex;align-items:center;gap:10px;padding:0 26px;font-size:12px;font-weight:600;color:var(--white);text-decoration:none;letter-spacing:.6px}
.topbar .book{background:var(--green);width:242px;justify-content:center}
.topbar .call{background:var(--teal);width:243px;justify-content:center}
.main-nav{position:absolute;top:62px;left:367px;display:flex;gap:45px;font-size:12px;font-weight:500;color:var(--ink)}
.main-nav span{position:relative}
.main-nav .active{color:var(--teal)}
.main-nav .active::after{content:"";position:absolute;left:-2px;right:-2px;top:31px;height:3px;background:var(--teal)}

/* hero */
.hero{position:absolute;left:0;top:100px;width:1200px;height:620px;background:linear-gradient(90deg,#eef1f1 0%,#e9eded 45%,#dfe3e2 100%);overflow:hidden}
.hero-photo{right:0;top:0;width:680px;height:620px;background:radial-gradient(ellipse at 60% 40%,#e8d4c6 0%,#c9d4dc 40%,#b8c6cf 65%,#dfe3e2 100%)}
.hero-text{position:absolute;left:40px;top:180px;width:560px;text-align:center}
.hero-text .kicker{font-size:20px;font-weight:400;color:var(--teal);letter-spacing:1.5px}
.hero-text h1{font-size:40px;font-weight:700;line-height:45px;margin-top:14px;letter-spacing:1.5px}
.hero-text h1 .l1{color:var(--teal);display:block}
.hero-text h1 .l2{color:var(--green);display:block}
.btn-solid{display:inline-flex;align-items:center;justify-content:center;border-radius:30px;color:var(--white);font-weight:600;letter-spacing:1px;background:linear-gradient(90deg,var(--teal),var(--green))}
.hero .btn-solid{position:absolute;left:204px;top:314px;width:234px;height:48px;font-size:13px}
.chev{position:absolute;width:30px;height:30px}

/* section heads */
.eyebrow{font-size:15px;font-weight:600;letter-spacing:3px;color:var(--teal)}
.title{font-size:36px;font-weight:700;letter-spacing:2px;color:var(--ink)}
.title .hl{color:var(--teal)}
.copy{font-family:"Open Sans",sans-serif;font-size:14px;line-height:29px;color:var(--body)}
.btn-outline{position:absolute;display:flex;align-items:center;justify-content:center;border:2px solid var(--teal);border-radius:30px;font-size:13px;font-weight:600;color:var(--teal);letter-spacing:1px}

/* about */
.about-text{position:absolute;left:635px;top:822px;width:478px}
.about-text .title{margin-top:6px}
.about-text .copy{margin-top:30px}

/* services */
.services{position:absolute;left:0;top:1296px;width:1200px;height:700px;background:linear-gradient(180deg,var(--teal) 0%,#178c84 60%,#1a948b 100%)}
.services-head{position:absolute;left:0;top:60px;width:1200px;text-align:center;color:var(--white)}
.services-head .eyebrow{color:var(--white);font-size:14px}
.services-head h2{font-size:29px;font-weight:700;letter-spacing:2px;margin-top:6px}
.services-head .rule{width:84px;height:3px;background:var(--green);margin:8px auto 0}
.card{position:absolute;overflow:hidden}
.card .label{position:absolute;left:0;right:0;bottom:18px;text-align:center;color:var(--white);font-weight:700;font-size:18px;letter-spacing:.5px}
.card-pt{left:104px;top:212px;width:311px;height:277px;background:linear-gradient(135deg,#8e9a9f,#4f6a6b 55%,#2b3f40)}
.card-wt{left:776px;top:212px;width:310px;height:277px;background:linear-gradient(135deg,#d9a77f,#b9825f 45%,#5a3e32)}
.card-ip{left:415px;top:188px;width:361px;height:325px;background:linear-gradient(160deg,#86c74d,#6db63a);box-shadow:0 10px 30px rgba(0,0,0,.2);text-align:center;color:var(--white);z-index:2}
.card-ip h3{margin-top:110px;font-size:18px;font-weight:700}
.card-ip p{font-family:"Open Sans",sans-serif;font-size:13px;line-height:21px;margin:12px auto 0;width:250px}
.card-ip .more{width:36px;height:36px;border:2px solid var(--white);border-radius:50%;margin:22px auto 0;display:flex;align-items:center;justify-content:center}

/* why */
.why-text{position:absolute;left:136px;top:2041px;width:400px}
.why-text .title{margin-top:6px;font-size:33px}
.why-text .copy{margin-top:26px}

/* stories */
.stories-head{position:absolute;left:0;top:2553px;width:1200px;text-align:center}
.stories-head h2{font-size:29px;font-weight:700;letter-spacing:2px;color:var(--teal)}
.stories-head .rule{width:94px;height:3px;background:var(--green);margin:9px auto 0}
.quote-card{position:absolute;left:597px;top:2645px;width:483px;height:383px;background:var(--white);box-shadow:0 4px 24px rgba(0,0,0,.1);z-index:2}
.quote-card .text{position:absolute;left:52px;top:105px;width:395px;font-family:"Open Sans",sans-serif;font-style:italic;font-size:13px;line-height:25.5px;color:var(--body)}
.quote-card .who{position:absolute;left:55px;top:270px;font-family:"Open Sans",sans-serif;font-weight:600;font-size:16px;color:var(--ink)}
.quote-card .where{position:absolute;left:55px;top:293px;font-family:"Open Sans",sans-serif;font-size:10px;color:var(--body)}
.dots{position:absolute;left:56px;top:330px;display:flex;gap:9px}
.dots span{width:9px;height:9px;border-radius:50%;background:#b9dedb}
.dots span:first-child{background:var(--teal-light)}

/* booking */
.booking{position:absolute;left:0;top:3157px;width:1200px;height:620px;background:linear-gradient(90deg,#1a978e 0%,#3fb2a8 30%,#d9eeec 60%,#eef4f4 100%);overflow:hidden}
.booking-photo{right:0;top:0;width:620px;height:620px;background:radial-gradient(ellipse at 55% 45%,#7fa8d6 0%,#b7c7d6 35%,#dfe7ea 70%,rgba(238,244,244,0) 100%)}
.booking-head{position:absolute;left:134px;top:88px;color:var(--white)}
.booking-head .eyebrow{color:var(--white);font-size:15px}
.booking-head h2{font-size:31px;font-weight:700;letter-spacing:2px;margin-top:2px}
.booking-head .rule{width:75px;height:3px;background:var(--green);margin-top:2px}
.field{position:absolute;left:130px;width:382px;height:42px;background:var(--white);border-radius:22px;font-family:"Open Sans",sans-serif;font-size:12px;color:var(--ink);padding:12px 25px}
.field.msg{height:93px;border-radius:18px;left:134px;width:378px}
.submit{position:absolute;left:135px;top:439px;width:154px;height:39px;font-size:12px}

/* footer */
.footer{position:absolute;left:0;top:3780px;width:1200px;height:286px;background:var(--white)}
.footer-brand{position:absolute;left:144px;top:60px;display:flex;flex-direction:column;align-items:center;gap:14px;width:200px}
.footer-brand .brand-dot{width:70px;height:70px}
.footer-brand .brand-name{font-size:40px}
.fcol{position:absolute;top:36px}
.fcol h4{font-size:16px;font-weight:700;color:var(--teal);letter-spacing:.5px}
.fcol ul{list-style:none;margin-top:10px}
.fcol li{font-family:"Open Sans",sans-serif;font-size:12px;line-height:28px;color:var(--ink)}
.fcol.contact li{display:flex;align-items:flex-start;gap:10px;line-height:23px}
.social{display:flex;gap:6px;margin-top:14px;margin-left:-8px}
.social span{width:26px;height:26px;border:2px solid var(--teal);border-radius:50%}
.bottom-bar{position:absolute;left:0;top:4066px;width:1200px;height:69px;background:var(--footer-bar);text-align:center;font-family:"Open Sans",sans-serif;font-size:12px;line-height:69px;color:var(--body)}
</style>
</head>
<body>

<header class="site-header">
  <div class="brand"><span class="brand-dot"></span><span class="brand-name">QUILL</span></div>
  <div class="topbar">
    <a class="book" href="#book">
      <svg width="15" height="15" viewBox="0 0 16 16" fill="none" stroke="#fff" stroke-width="1.6"><rect x="2" y="3" width="12" height="11" rx="1"/><path d="M2 6.5h12M5 1.5v3M11 1.5v3"/></svg>
      BOOK APPOINTMENT</a>
    <a class="call" href="#call">
      <svg width="14" height="14" viewBox="0 0 16 16" fill="#fff"><path d="M3.6 1.5l2.2 2.6-1.3 1.8c.9 2 2.4 3.6 4.5 4.6l1.8-1.4 2.7 2.2-1.1 2.3C7.2 13.4 2.7 8.9 1.4 3z"/></svg>
      CALL US +1 555 010 2468</a>
  </div>
  <nav class="main-nav">
    <span class="active">HOME</span><span>ABOUT US</span><span>OUR SERVICES</span><span>WHY CHOOSE US</span><span>TESTIMONIALS</span><span>CONTACT US</span>
  </nav>
</header>

<section class="hero">
  <div class="photo hero-photo" role="img" aria-label="Therapist adjusting a patient's neck and shoulder"></div>
  <div class="hero-text">
    <div class="kicker">WELCOME TO</div>
    <h1><span class="l1">QUILL PHYSICAL</span><span class="l2">THERAPY &amp; WELLNESS</span></h1>
  </div>
  <a class="btn-solid" href="#book">BOOK APPOINTMENT</a>
  <svg class="chev" style="left:22px;top:287px" viewBox="0 0 30 30" fill="none" stroke="#fff" stroke-width="3"><path d="M20 4L9 15l11 11"/></svg>
  <svg class="chev" style="left:1153px;top:287px" viewBox="0 0 30 30" fill="none" stroke="#fff" stroke-width="3"><path d="M10 4l11 11-11 11"/></svg>
</section>

<!-- hero to about transition and about image -->
<svg class="abs" style="left:0;top:640px" width="1200" height="660" viewBox="0 640 1200 660">
  <defs>
    <linearGradient id="backGrad" x1="0" y1="0" x2="1" y2="1">
      <stop offset="0" stop-color="#f0c8b0"/><stop offset=".5" stop-color="#f28f6a"/><stop offset="1" stop-color="#d9a48c"/>
    </linearGradient>
  </defs>
  <path d="M0 720 Q 600 610 1200 720 L1200 1300 L0 1300 Z" fill="#fff"/>
  <path d="M200 685 Q 620 620 1050 708" fill="none" stroke="var(--green)" stroke-width="6"/>
  <path d="M0 714 L380 714 Q 470 760 500 860 Q 520 1130 640 1296 L0 1296 Z" fill="var(--green)"/>
  <path d="M0 714 L360 714 Q 455 760 478 860 Q 470 1130 600 1296 L0 1296 Z" fill="var(--teal)"/>
  <path d="M0 730 L330 730 Q 430 770 450 870 Q 440 1140 575 1296 L0 1296 Z" fill="url(#backGrad)" role="img" aria-label="Hands massaging a patient's back over a highlighted spine"/>
</svg>

<div class="about-text">
  <div class="eyebrow">WHO WE ARE</div>
  <div class="title">ABOUT <span class="hl">QUILL</span></div>
  <p class="copy">Lorem Ipsum is simply dummy text of the printing and typesetting industry. Lorem Ipsum has been the industry's standard dummy text ever since the 1500s, when an unknown printer took a galley of type and scrambled it to make a type specimen book. It has survived not only five centuries, but also the leap into electronic typesetting, remaining essentially unchanged. Lorem Ipsum is simply dummy.</p>
</div>
<a class="btn-outline" style="left:632px;top:1126px;width:167px;height:46px">LEARN MORE</a>

<section class="services">
  <div class="services-head">
    <div class="eyebrow">WHAT WE DO</div>
    <h2>SERVICES PROVIDE</h2>
    <div class="rule"></div>
  </div>
  <div class="card card-pt" role="img" aria-label="Therapist stretching a patient's leg"><div class="label">PHYSICAL THERAPY</div></div>
  <div class="card card-ip">
    <h3>INJURY PAIN</h3>
    <p>Lorem ipsum dolor sit amet, consectetur adipiscing elit sed or sit amet consectetur adipiscing.</p>
    <div class="more"><svg width="16" height="16" viewBox="0 0 16 16" fill="none" stroke="#fff" stroke-width="2"><path d="M3 6l5 5 5-5"/></svg></div>
  </div>
  <div class="card card-wt" role="img" aria-label="Relaxing head massage with candles"><div class="label">WELLNESS THERAPY</div></div>
  <svg class="chev" style="left:48px;top:340px" viewBox="0 0 30 30" fill="none" stroke="#fff" stroke-width="3"><path d="M20 4L9 15l11 11"/></svg>
  <svg class="chev" style="left:1105px;top:340px" viewBox="0 0 30 30" fill="none" stroke="#fff" stroke-width="3"><path d="M10 4l11 11-11 11"/></svg>
</section>

<!-- why choose -->
<svg class="abs" style="left:0;top:1880px" width="1200" height="640" viewBox="0 1880 1200 640">
  <defs>
    <linearGradient id="whyPhoto" x1="0" y1="0" x2="1" y2="0">
      <stop offset="0" stop-color="#eef3f3"/><stop offset=".35" stop-color="#d9dcd8"/><stop offset=".7" stop-color="#c7cdc4"/><stop offset="1" stop-color="#e4e6e2"/>
    </linearGradient>
  </defs>
  <path d="M0 1975 Q 620 1840 1200 1980 L1200 2420 Q 620 2560 0 2420 Z" fill="var(--mist)"/>
  <path d="M520 1935 Q 860 1880 1200 1980 L1200 2420 Q 860 2510 520 2500 Z" fill="url(#whyPhoto)" role="img" aria-label="Therapist treating a patient lying on a mat"/>
  <path d="M880 1915 Q 1060 1930 1200 1995" fill="none" stroke="var(--green)" stroke-width="7"/>
  <path d="M0 2420 Q 320 2505 700 2500" fill="none" stroke="var(--green)" stroke-width="7"/>
</svg>

<div class="why-text">
  <div class="eyebrow">WHY WE ARE</div>
  <div class="title">WHY CHOOSE <span class="hl">QUILL</span></div>
  <p class="copy">Lorem Ipsum is simply dummy text of the printing and typesetting industry. Lorem Ipsum has been the industry's standard dummy text ever since the 1500s, when an unknown printer took a galley of type and scrambled it to make a type specimen book. It has survived</p>
</div>
<a class="btn-outline" style="left:135px;top:2305px;width:162px;height:46px">LEARN MORE</a>

<!-- success stories -->
<div class="stories-head"><h2>SUCCESS STORIES</h2><div class="rule"></div></div>
<div class="abs" style="left:99px;top:2634px;width:157px;height:12px;background:var(--green)"></div>
<div class="abs" style="left:99px;top:2634px;width:12px;height:75px;background:var(--green)"></div>
<div class="photo" style="left:112px;top:2645px;width:485px;height:383px;background:linear-gradient(90deg,#6fb0d6 0%,#c9d2d6 45%,#8a8f92 75%,#d7d9d8 100%)" role="img" aria-label="Therapist helping a smiling patient stretch his arm"></div>
<svg class="abs" style="left:325px;top:2810px" width="54" height="54" viewBox="0 0 54 54"><circle cx="27" cy="27" r="26" fill="#fff"/><path d="M21 16l18 11-18 11z" fill="#444"/></svg>
<div class="abs" style="left:934px;top:3026px;width:157px;height:12px;background:var(--teal)"></div>
<div class="abs" style="left:1080px;top:2932px;width:11px;height:106px;background:var(--teal)"></div>
<div class="quote-card">
  <svg class="abs" style="left:50px;top:48px" width="58" height="40" viewBox="0 0 58 40" fill="var(--green)"><path d="M2 38V22C2 10 8 3 20 1l2 5c-7 2-10 6-10 12h10v20zM34 38V22C34 10 40 3 52 1l2 5c-7 2-10 6-10 12h10v20z"/></svg>
  <p class="text">Lorem ipsum dolor sit amet, consectetur adipiscing elit, sed do eiusmod tempor incididunt ut labore et dolore magna aliqua. Ut enim ad minim veniam, quis nostrud exercitation ullamco laboris nisi ut aliquip ex ea commodo consequat. Duis aute irure dolor in reprehenderit in voluptate velit esse cillum dolore eu fugiat nulla pariatur. Excepteur s</p>
  <div class="who">Patient Name</div>
  <div class="where">Location Area</div>
  <div class="dots"><span></span><span></span><span></span><span></span></div>
</div>

<!-- booking -->
<section class="booking" id="book">
  <div class="photo booking-photo" role="img" aria-label="Therapist guiding an older patient exercising on a ball"></div>
  <div class="booking-head">
    <div class="eyebrow">GET IN TOUCH</div>
    <h2>BOOK APPOINTMENT</h2>
    <div class="rule"></div>
  </div>
  <div class="field" style="top:174px">Name*</div>
  <div class="field" style="top:226px">Email address*</div>
  <div class="field" style="top:276px">Phone*</div>
  <div class="field msg" style="top:332px">Message</div>
  <a class="btn-solid submit" style="background:var(--green)">SUBMIT NOW</a>
</section>

<svg class="abs" style="left:0;top:3690px" width="1200" height="100" viewBox="0 3690 1200 100">
  <path d="M0 3790 L0 3775 Q 560 3680 1200 3745 L1200 3790 Z" fill="#fff"/>
  <path d="M80 3762 Q 600 3685 1200 3730" fill="none" stroke="var(--green)" stroke-width="5"/>
</svg>

<footer class="footer">
  <div class="footer-brand"><span class="brand-dot"></span><span class="brand-name">QUILL</span></div>
  <div class="fcol" style="left:441px">
    <h4>NAVIGATE</h4>
    <ul><li>Home</li><li>About Us</li><li>Our Services</li><li>New Products</li><li>Contact Us</li></ul>
  </div>
  <div class="fcol" style="left:638px">
    <h4>RESOURCES</h4>
    <ul><li>News</li><li>Testimonials</li><li>Privacy Policy</li><li>Terms &amp; Condition</li></ul>
  </div>
  <div class="fcol contact" style="left:855px">
    <h4>CONTACT US</h4>
    <ul>
      <li><svg width="12" height="14" viewBox="0 0 12 14" style="margin-top:4px"><path d="M6 0a5 5 0 015 5c0 4-5 9-5 9S1 9 1 5a5 5 0 015-5z" fill="var(--teal)"/><circle cx="6" cy="5" r="2" fill="#fff"/></svg><span>Office Lindenfeld | Birchway Lane 14<br>Office Harrowgate | Elm Court 8</span></li>
      <li><svg width="12" height="12" viewBox="0 0 16 16" fill="var(--teal)" style="margin-top:5px"><path d="M3.6 1.5l2.2 2.6-1.3 1.8c.9 2 2.4 3.6 4.5 4.6l1.8-1.4 2.7 2.2-1.1 2.3C7.2 13.4 2.7 8.9 1.4 3z"/></svg><span>Tel: (1300) 555 0182</span></li>
      <li><svg width="12" height="10" viewBox="0 0 12 10" style="margin-top:6px"><rect width="12" height="10" fill="var(--teal)"/><path d="M0 0l6 5 6-5" fill="none" stroke="#fff"/></svg><span>Email: hello@quillphysio.example</span></li>
    </ul>
    <div class="social"><span></span><span></span><span></span></div>
  </div>
</footer>
<div class="bottom-bar">© 2021 Brightmoor Studio | All Rights Reserved &nbsp;|&nbsp; Terms &amp; Condition</div>

</body>
</html>
```